Upmarket Dessert Lounge needs a Business Card Design

We are an upmarket dessert lounge needing a business card to match our image.

We want something that is simple yet beautiful, feminine, classy, sophisticated and elegant. We want it to stand out and don't mind if it is bold.

The design should include our logo and colours of red or maroon with gold highlights. We don't mind if black is used.

Marlow & Quince

Target Market(s)

For those who like to indulge or treat themselves and give in to their temptations on good quality desserts.

Industry/Entity Type

Business

Requirements
Must have
• Must include our logo and our name

Marlow & Quince

M & Q

```html
<!DOCTYPE html>
<html lang="en">
<head>
<meta charset="utf-8">
<title>Marlow &amp; Quince — Business Card</title>
<link rel="stylesheet" href="https://fonts.googleapis.com/css2?family=Source+Sans+3:wght@400;600;700&display=swap">
<style>
  :root {
    --maroon: #7a1416;
    --gold: #fdd39b;
    --ink: #333333;
    --card: #ffffff;
    --backdrop: #e9e9e9;
  }
  html, body {
    margin: 0;
    padding: 0;
    overflow: hidden;
  }
  body {
    width: 956px;
    height: 1200px;
    background: var(--backdrop);
    position: relative;
    font-family: "Source Sans 3", "Myriad Pro", Arial, sans-serif;
    color: var(--ink);
  }
  .card {
    position: absolute;
    width: 798px;
    height: 455px;
    background: var(--card);
    border-radius: 26px;
    overflow: hidden;
  }
  .card--front { left: 79px; top: 98px; }
  .card--back  { left: 73px; top: 632px; }

  .card__waves {
    position: absolute;
    left: 0;
    top: 0;
    width: 798px;
    height: 455px;
  }
  .wave--maroon { fill: var(--maroon); }
  .wave--gold { fill: var(--gold); }

  .brand-name {
    position: absolute;
    color: var(--maroon);
    font-weight: 600;
    white-space: nowrap;
    text-align: center;
    letter-spacing: 0.04em;
  }
  .card--front .brand-name {
    left: 24px;
    width: 380px;
    top: 150px;
    font-size: 31px;
    line-height: 44px;
  }
  .card--back .brand-name {
    left: 0;
    width: 798px;
    top: 160px;
    font-size: 110px;
    line-height: 136px;
    letter-spacing: 0.02em;
  }

  .contact {
    position: absolute;
    left: 433px;
    top: 82px;
  }
  .contact__name {
    font-size: 23px;
    font-weight: 700;
    line-height: 28px;
    margin: 0;
  }
  .contact__role {
    font-size: 23px;
    line-height: 28px;
    margin: 0 0 14px;
    letter-spacing: 0.02em;
  }
  .contact__lines {
    list-style: none;
    margin: 0 0 18px;
    padding: 0;
    font-size: 19px;
    line-height: 30px;
  }
  .contact__label { font-weight: 700; }
  .contact__address {
    font-size: 19px;
    line-height: 27px;
    margin: 0;
    font-style: normal;
  }
  .card__footer {
    position: absolute;
    left: 0;
    width: 798px;
    top: 410px;
    text-align: center;
    color: #ffffff;
    font-size: 19px;
    line-height: 26px;
  }
  .card__footer b { font-weight: 700; }
  .card__footer .divider { margin: 0 8px; }
</style>
</head>
<body>

  <section class="card card--front">
    <svg class="card__waves" viewBox="0 0 798 455" aria-hidden="true">
      <path class="wave--gold" d="M520,378 C650,372 760,325 798,240 L798,290 C760,340 650,376 520,378 Z"/>
      <path class="wave--maroon" d="M0,395 C60,360 200,355 330,365 C450,375 530,385 565,385 C680,380 760,340 798,300 L798,455 L0,455 Z"/>
    </svg>

    <div class="brand-name">MARLOW &amp; QUINCE</div>

    <div class="contact">
      <p class="contact__name">Your Name</p>
      <p class="contact__role">Designation</p>
      <ul class="contact__lines">
        <li><span class="contact__label">p</span> : 123-456-7890</li>
        <li><span class="contact__label">c</span> : 123-456-7890</li>
        <li><span class="contact__label">f</span> : 123-456-7890</li>
      </ul>
      <address class="contact__address">0000, Street Name<br>City Name, Country Code.</address>
    </div>

    <div class="card__footer">
      <b>e</b> : name@yourwebsite.com <span class="divider">|</span> <b>w</b> : www.marlow&amp;quince.com
    </div>
  </section>

  <section class="card card--back">
    <div class="brand-name">M &amp; Q</div>
  </section>

</body>
</html>
```